Bright Towns Forum PowerPoint Design Template and Sample Deck

The Bright Towns Forum is an international organization that seeks to improve the livability, workability and sustainability of the world’s cities.
We seek a versatile PowerPoint design template with 10 slide types plus a “self-documenting” sample deck. Your design will be used in keynote speeches and workshops around the world.
After the contest is completed, we will ask the winning designer to add 10-20 additional slide types for $75 per slide. We also seek a long-term relationship whereby we can request “custom” slides and/or ask the designer to touch up the slides we build to make them better.
FILES. We have uploaded several files:
2. PALETTE. Shows our official colors.
3 LOGOS. Several individual files with different variations of our logo. Some with our motto, some without.
2. SAMPLE SLIDES. Because we were unable to successfully upload our sample deck, we are making it available via this FileNook link:
https://www.filenook-example.com/s/k7qrtmzp2wd9hxa/The%20Bright%20Towns%20Forum%20Design%20Contest%20Notes.docx?dl=0
Target Market(s)
Mayors, department heads, CIOs, senior executives from technology companies
Industry/Entity Type
Information Technology
Colors
Designer to choose colors to be used in the design.
Requirements
Must have
- Please see uploaded Word document for requirements, nice to haves and should not haves and uploaded palette for color preferences.
Nice to have
- see above
Should not have
- see above

```html
<!DOCTYPE html>
<html lang="en">
<head>
<meta charset="utf-8">
<title>Bright Towns Forum — Slide Template</title>
<link href="https://fonts.googleapis.com/css2?family=Open+Sans:ital,wght@0,400;0,600;0,700;1,400;1,600&family=Montserrat:wght@600;700&display=swap" rel="stylesheet">
<style>
:root{
  --navy:#163a6b;
  --blue:#2a62b0;
  --sky:#5a8fd8;
  --orange:#f7941d;
  --purple:#8a55b0;
  --pink:#d2448a;
  --green:#7aab3a;
  --gray:#9a9a9a;
  --ink:#555c66;
  --page:#e9e6e1;
  --white:#ffffff;
}
*{box-sizing:border-box;margin:0;padding:0}
html,body{width:1200px;height:1200px;overflow:hidden}
body{background:var(--page);font-family:"Open Sans",Arial,sans-serif;color:var(--ink);position:relative}
.slide{position:absolute;width:360px;height:203px;overflow:hidden;background:var(--white);box-shadow:0 4px 14px rgba(0,0,0,.18)}
.c1{left:30px}.c2{left:420px}.c3{left:810px}
.r1{top:149px}.r2{top:382px}.r3{top:615px}.r4{top:848px}
.title{font-weight:600;color:var(--blue);font-size:15px;text-align:center;padding-top:14px}
.dots{display:block;text-align:center;color:var(--blue);font-size:8px;letter-spacing:1px;line-height:8px}
.footer{position:absolute;left:0;right:0;bottom:0;height:20px;background:var(--navy);display:flex;align-items:center;justify-content:space-between;padding:0 10px}
.brand{color:var(--white);font-size:9px;font-weight:600}
.folio{color:#b9c7de;font-size:5px;display:flex;align-items:center;gap:5px}
.folio b{background:var(--blue);color:#fff;width:10px;height:10px;display:inline-flex;align-items:center;justify-content:center;font-size:5px}
.tiny{font-size:4.5px;line-height:6px;color:#8a9099}
.lbl{font-size:5.5px;color:var(--ink);font-weight:600}

/* agenda chevrons */
.chev-row{display:flex;justify-content:space-around;padding:14px 12px 0}
.chev-item{display:flex;flex-direction:column;align-items:center;width:60px}
.chev{width:56px;height:14px;margin:5px 0 8px;clip-path:polygon(0 0,85% 0,100% 50%,85% 100%,0 100%,12% 50%)}
.ring{width:26px;height:26px;border-radius:50%;border:1.5px solid;display:flex;align-items:center;justify-content:center;font-size:8px;font-weight:600}

/* hero */
.hero{background:linear-gradient(160deg,#2c67ad,#1d4c8c)}
.hero .photo{position:absolute;inset:0;background:linear-gradient(180deg,rgba(255,255,255,0) 30%,rgba(120,160,210,.35));}
.hero h1{position:absolute;top:40px;width:100%;text-align:center;color:#fff;font-size:24px;font-weight:600}
.hero h1 span{color:var(--orange)}
.hero p{position:absolute;top:84px;width:100%;text-align:center;color:#e6eefa;font-size:8px;font-style:italic}

/* section */
.section{background:linear-gradient(135deg,#9462bb,#7f4aa8)}
.section .cap{position:absolute;right:30px;bottom:50px;text-align:right;color:#fff}
.section .cap strong{font-size:11px;font-weight:600;display:block}
.section .cap em{font-size:7px}
.arrow-dot{position:absolute;right:14px;bottom:52px}

/* skyline agenda */
.hand{position:absolute;left:20px;top:56px;width:34px;height:40px;border-radius:6px;background:linear-gradient(#f5d7b8,#e9b98f)}
.mini-brand{position:absolute;left:58px;top:74px;font-size:8px;font-weight:600;color:var(--navy);line-height:9px}
.track{position:absolute;left:50px;right:20px;top:52px;height:1px;background:var(--green)}
.node{position:absolute;text-align:center;width:60px}
.node i{display:block;margin:0 auto 3px;width:18px;height:18px;border-radius:50%}
.skyline{position:absolute;left:0;right:0;bottom:20px;height:48px;background:linear-gradient(var(--green),#6a9a30)}

/* quote */
.quote{background:linear-gradient(120deg,#5b6478,#434b5e)}
.quote .txt{position:absolute;left:16px;top:24px;width:170px;color:#fff;font-size:8.5px;font-style:italic;line-height:12px}
.quote .txt span{color:var(--orange);font-weight:600}
.quote .who{margin-top:8px;font-style:normal;font-size:6.5px;font-weight:600;line-height:8px}
.quote .portrait{position:absolute;right:0;top:0;bottom:0;width:150px;background:linear-gradient(160deg,#8c98b4,#c28a74 70%,#e99c8a)}

/* 3d bars */
.blocks{position:absolute;left:20px;right:20px;bottom:30px;display:flex;justify-content:space-between;align-items:flex-end}
.block{width:52px;position:relative}
.block .top{height:8px;transform:skewX(-30deg);transform-origin:bottom;filter:brightness(1.2)}
.block .face{display:flex;align-items:flex-start;justify-content:center;color:#fff;font-size:5px;padding-top:4px}
.labels{display:flex;justify-content:space-between;padding:8px 20px 0}

/* stats text slide */
.big{font-size:20px;font-weight:700;color:var(--blue)}
.colL{position:absolute;left:16px;top:48px;width:150px}
.colR{position:absolute;left:190px;top:54px;width:150px}

/* pink stats */
.pink .photo{position:absolute;inset:0;background:linear-gradient(135deg,#cf4f90,#b9387b)}
.pink .title{color:#fff;position:relative}
.pink .dots{color:#fff;position:relative}
.stats{position:relative;display:flex;justify-content:space-around;padding:10px 14px 0;color:#fff}
.stat{text-align:center}
.stat strong{font-size:16px;font-weight:400;display:block}
.stat small{font-size:5px;color:#fbe0ee}
.pink .body{position:relative;color:#fbe0ee;font-size:5px;line-height:7px;padding:12px 24px 0;text-align:center}

/* photo list */
.audience{position:absolute;left:0;top:0;bottom:20px;width:150px;background:linear-gradient(160deg,#cfd5dc,#5e6672)}
.checklist{position:absolute;left:164px;top:48px;right:12px;list-style:none}
.checklist li{display:flex;gap:5px;margin-bottom:7px}
.checklist svg{flex:none}

/* timeline chart */
.chart{position:absolute;left:18px;right:18px;top:44px;height:110px}

/* map */
.mapslide{background:var(--navy)}
.mapslide .title{color:#fff}
.mapslide .dots{color:#fff}
.worldmap{position:absolute;left:14px;top:48px;width:200px;height:120px;border-radius:4px;background:linear-gradient(135deg,#eaf0f8,#c7d4e6)}
.mapslide .tiny{position:absolute;left:230px;top:70px;width:115px;color:#c2cde0}

/* label */
.format{position:absolute;left:810px;top:848px;width:360px;height:203px;display:flex;align-items:center;justify-content:center}
.format div{border:1.5px solid #8c8880;padding:18px 30px;font-family:"Montserrat","Open Sans",sans-serif;font-weight:700;font-size:22px;color:#4a4740;text-align:center;letter-spacing:1px;line-height:28px}
</style>
</head>
<body>

<!-- Row 1 -->
<section class="slide c1 r1">
  <h2 class="title">Progressive Agenda</h2><span class="dots">•••••</span>
  <div class="chev-row">
    <div class="chev-item"><span class="lbl">Your Agenda - 01</span><span class="tiny">Short note here</span><i class="chev" style="background:var(--purple)"></i><span class="ring" style="border-color:var(--purple);color:var(--purple)">01</span></div>
    <div class="chev-item"><span class="lbl">Your Agenda - 02</span><span class="tiny">Short note here</span><i class="chev" style="background:var(--orange)"></i><span class="ring" style="border-color:var(--orange);color:var(--orange)">02</span></div>
    <div class="chev-item"><span class="lbl">Your Agenda - 03</span><span class="tiny">Short note here</span><i class="chev" style="background:var(--gray)"></i><span class="ring" style="border-color:var(--gray);color:var(--gray)">03</span></div>
    <div class="chev-item"><span class="lbl">Your Agenda - 04</span><span class="tiny">Short note here</span><i class="chev" style="background:var(--green)"></i><span class="ring" style="border-color:var(--green);color:var(--green)">04</span></div>
    <div class="chev-item"><span class="lbl">Your Agenda - 05</span><span class="tiny">Short note here</span><i class="chev" style="background:var(--sky)"></i><span class="ring" style="border-color:var(--sky);color:var(--sky)">05</span></div>
  </div>
  <div class="footer"><span class="brand">Bright Towns Forum</span><span class="folio">Copyright 2017 <b>4</b></span></div>
</section>

<section class="slide c2 r1 hero">
  <div class="photo" role="img" aria-label="City skyline photograph tinted blue"></div>
  <h1>The world is <span>changing</span></h1>
  <p>“The biggest shift in economic gravity in history.”<br>Halvorsen &amp; Partners</p>
</section>

<section class="slide c3 r1 section">
  <div class="cap"><strong>1 Progressive Agenda</strong><em>Slide ideas...</em></div>
  <svg class="arrow-dot" width="12" height="12" viewBox="0 0 12 12"><circle cx="6" cy="6" r="5" fill="none" stroke="#fff"/><path d="M5 3.5 7.5 6 5 8.5" fill="none" stroke="#fff"/></svg>
</section>

<!-- Row 2 -->
<section class="slide c1 r2">
  <h2 class="title" style="padding-left:60px">Progressive Agenda</h2><span class="dots" style="padding-left:60px">•••••</span>
  <div class="track"></div>
  <div class="node" style="left:88px;top:44px"><i style="background:var(--gray)"></i><span class="lbl">Your Agenda - 01</span></div>
  <div class="node" style="left:150px;top:44px"><i style="background:var(--orange)"></i><span class="lbl">Your Agenda - 02</span></div>
  <div class="node" style="left:212px;top:44px"><i style="background:var(--orange)"></i><span class="lbl">Your Agenda - 03</span></div>
  <div class="node" style="left:274px;top:44px"><i style="background:var(--purple)"></i><span class="lbl">Your Agenda - 04</span></div>
  <div class="hand" role="img" aria-label="Hand pressing a touch icon"></div>
  <div class="mini-brand">Bright<br>Towns<br>Forum</div>
  <div class="skyline" role="img" aria-label="Green city skyline silhouette"></div>
  <div class="footer"><span class="brand">Bright Towns Forum</span><span class="folio">Copyright 2017 <b>11</b></span></div>
</section>

<section class="slide c2 r2 quote">
  <div class="portrait" role="img" aria-label="Portrait photograph of the speaker"></div>
  <div class="txt">“For those of us living in cities, we need to make sure they are smart cities. <span>Nothing else makes sense.</span> And nothing else is such a world-wide <span>economic opportunity.</span>”
    <div class="who">Marta Linden<br>Vice President<br>Continental Policy Board</div>
  </div>
</section>

<section class="slide c3 r2">
  <h2 class="title">Progressive Agenda</h2><span class="dots">•••••</span>
  <div class="labels">
    <span class="lbl">Your Agenda - 01</span><span class="lbl">Your Agenda - 02</span><span class="lbl">Your Agenda - 03</span><span class="lbl">Your Agenda - 04</span>
  </div>
  <div class="blocks">
    <div class="block"><div class="top" style="background:var(--purple)"></div><div class="face" style="height:40px;background:linear-gradient(var(--purple),#c8b0da)">Your Text</div></div>
    <div class="block"><div class="top" style="background:var(--green)"></div><div class="face" style="height:52px;background:linear-gradient(var(--green),#cfe1b5)">Your Text</div></div>
    <div class="block"><div class="top" style="background:var(--gray)"></div><div class="face" style="height:64px;background:linear-gradient(var(--gray),#dcdcdc)">Your Text</div></div>
    <div class="block"><div class="top" style="background:var(--orange)"></div><div class="face" style="height:76px;background:linear-gradient(var(--orange),#fbd3a0)">Your Text</div></div>
    <div class="block"><div class="top" style="background:var(--sky)"></div><div class="face" style="height:88px;background:linear-gradient(var(--sky),#c8daf2)">Your Text</div></div>
  </div>
  <div class="footer"><span class="brand">Bright Towns Forum</span><span class="folio">Copyright 2017 <b>7</b></span></div>
</section>

<!-- Row 3 -->
<section class="slide c1 r3">
  <h2 class="title" style="text-align:left;padding-left:16px">Your Slide Title Here</h2><span class="dots" style="text-align:left;padding-left:16px">•••••</span>
  <div class="colL"><span class="big">66%</span><p class="tiny">Add a short line of supporting text here to explain this figure and its context for the audience.</p>
    <p class="big" style="font-size:11px;margin-top:14px">12%</p><p class="tiny">Enter your text here</p></div>
  <div class="colR"><p class="lbl" style="font-size:8px">45%</p><p class="tiny">Suitable for all categories of business and public services. Add your own text here to describe the result, the source and the trend over the year.</p></div>
  <div class="footer"><span class="brand">Bright Towns Forum</span><span class="folio">Copyright 2017 <b>27</b></span></div>
</section>

<section class="slide c2 r3 pink">
  <div class="photo" role="img" aria-label="Workshop audience photograph tinted pink"></div>
  <h2 class="title">Your Slide Title Here</h2><span class="dots">•••••</span>
  <div class="stats">
    <div class="stat"><strong>101</strong><small>Your Text Here</small></div>
    <div class="stat"><strong>25150</strong><small>Your Text Here</small></div>
    <div class="stat"><strong>672</strong><small>Your Text Here</small></div>
    <div class="stat"><strong>980</strong><small>Your Text Here</small></div>
  </div>
  <p class="body">Add a short paragraph here that sums up these numbers, where they come from and why they matter to the towns and partners taking part in the programme.</p>
  <div class="footer"><span class="brand">Bright Towns Forum</span><span class="folio">Copyright 2017 <b>26</b></span></div>
</section>

<section class="slide c3 r3">
  <div class="audience" role="img" aria-label="Conference hall audience photograph"></div>
  <h2 class="title" style="padding-left:150px">Your Slide Title Here</h2><span class="dots" style="padding-left:150px">•••••</span>
  <ul class="checklist">
    <li><svg width="8" height="8" viewBox="0 0 8 8"><circle cx="4" cy="4" r="4" fill="var(--green)"/><path d="M2 4.2 3.4 5.5 6 2.7" stroke="#fff" fill="none"/></svg><div><span class="lbl">Enter Your Title Here</span><p class="tiny">Add a short supporting line here</p></div></li>
    <li><svg width="8" height="8" viewBox="0 0 8 8"><circle cx="4" cy="4" r="4" fill="var(--green)"/><path d="M2 4.2 3.4 5.5 6 2.7" stroke="#fff" fill="none"/></svg><div><span class="lbl">Enter Your Title Here</span><p class="tiny">Add a short supporting line here</p></div></li>
    <li><svg width="8" height="8" viewBox="0 0 8 8"><circle cx="4" cy="4" r="4" fill="var(--green)"/><path d="M2 4.2 3.4 5.5 6 2.7" stroke="#fff" fill="none"/></svg><div><span class="lbl">Enter Your Title Here</span><p class="tiny">Add a short supporting line here</p></div></li>
  </ul>
  <div class="footer"><span class="brand">Bright Towns Forum</span><span class="folio">Copyright 2017 <b>9</b></span></div>
</section>

<!-- Row 4 -->
<section class="slide c1 r4">
  <h2 class="title">One Year Timeline</h2><span class="dots">•••••</span>
  <svg class="chart" viewBox="0 0 324 110">
    <line x1="0" y1="70" x2="324" y2="70" stroke="#c9ccd1"/>
    <g font-family="Open Sans, sans-serif" font-size="5" fill="#8a9099" text-anchor="middle">
      <rect x="12" y="20" width="7" height="50" fill="var(--navy)"/><circle cx="15.5" cy="70" r="2.5" fill="#c9ccd1"/><text x="15.5" y="80">JAN</text>
      <rect x="40" y="48" width="7" height="22" fill="var(--blue)"/><circle cx="43.5" cy="70" r="2.5" fill="#c9ccd1"/><text x="43.5" y="80">FEB</text>
      <circle cx="71" cy="70" r="2.5" fill="#c9ccd1"/><text x="71" y="80">MAR</text>
      <rect x="96" y="30" width="7" height="40" fill="var(--sky)"/><circle cx="99.5" cy="70" r="2.5" fill="#c9ccd1"/><text x="99.5" y="80">APR</text>
      <circle cx="127" cy="70" r="2.5" fill="#c9ccd1"/><text x="127" y="80">MAY</text>
      <rect x="152" y="38" width="7" height="32" fill="#e8452c"/><circle cx="155.5" cy="70" r="2.5" fill="#c9ccd1"/><text x="155.5" y="80">JUN</text>
      <circle cx="183" cy="70" r="2.5" fill="#c9ccd1"/><text x="183" y="80">JUL</text>
      <rect x="208" y="44" width="7" height="26" fill="var(--orange)"/><circle cx="211.5" cy="70" r="2.5" fill="#c9ccd1"/><text x="211.5" y="80">AUG</text>
      <circle cx="239" cy="70" r="2.5" fill="#c9ccd1"/><text x="239" y="80">SEP</text>
      <rect x="264" y="52" width="7" height="18" fill="#6e6e6e"/><circle cx="267.5" cy="70" r="2.5" fill="#c9ccd1"/><text x="267.5" y="80">OCT</text>
      <rect x="300" y="36" width="7" height="34" fill="var(--gray)"/><circle cx="303.5" cy="70" r="2.5" fill="#c9ccd1"/><text x="303.5" y="80">DEC</text>
      <text x="162" y="96" font-size="4.5">Add a short line of text to describe the key milestones reached across the year.</text>
    </g>
  </svg>
  <div class="footer"><span class="brand">Bright Towns Forum</span><span class="folio">Copyright 2017 <b>14</b></span></div>
</section>

<section class="slide c2 r4 mapslide">
  <h2 class="title">Your Slide Title Here</h2><span class="dots">•••••</span>
  <div class="worldmap" role="img" aria-label="World map with location markers"></div>
  <p class="tiny">Add a short paragraph here about the regions shown on the map, where members are based and how the network has grown across continents over recent years.</p>
</section>

<div class="format"><div>16:9 WIDESCREEN<br>DISPLAY</div></div>

</body>
</html>
```